ULMIRA card Technical Architecture

Hello everyone ULMIRA: It is a consulting firm in Architecture and Construction. I require a card duplexing, sober, elegant, classic but not boring. Update 1: Use the following data for the card. Name: Gonzalo Pereda Mauricio Villalta Position: COO Twitter: @ulmiraAT Homepage: ulmira-example.com home address not include the participation of all thank you.

Target Market(s)

Construction companies, Architects and Consulting Engineers

Industry/Entity Type

Consulting

Contact Information for Business Card

Los campos que debe tener:
Nombre, Cargo, email, homepage y twitter

Font styles to use
Serif
Sans Serif
Other font styles liked:
• Me gustan playfair display, open sans y roboto, pero estoy sujeto a sus propuestas

Requirements
Must have
• Colors: Present combined proposals in white, red, gray and black Update 1: The two names must be clearly differentiated from the two surnames
Nice to have
• They are free to present their best proposals. I will bring them immediate feedback to the extent you can go see their designs. Complete data for card and logo files will give the winner the

```html
<!DOCTYPE html>
<html lang="es">
<head>
<meta charset="utf-8">
<title>ULMIRA – Tarjetas de presentación</title>
<link rel="stylesheet" href="https://fonts.googleapis.com/css2?family=Montserrat:wght@400;500;700&display=swap">
<style>
  :root {
    --bg: #e6e6e6;
    --black: #050505;
    --red: #d1262b;
    --wine: #6e0d10;
    --gray: #3a3a3a;
    --ink: #222222;
    --white: #ffffff;
    --rule: #9a9a9a;
  }
  * { box-sizing: border-box; margin: 0; padding: 0; }
  html, body { width: 1200px; height: 900px; overflow: hidden; }
  body { background: var(--bg); font-family: "Montserrat", sans-serif; position: relative; }

  .card {
    position: absolute;
    width: 560px; height: 320px;
    border-radius: 18px;
    overflow: hidden;
    box-shadow: 0 10px 24px rgba(0,0,0,.25);
  }
  .card-shapes { position: absolute; inset: 0; width: 100%; height: 100%; }

  /* Front */
  .card-front { left: 70px; top: 100px; background: var(--black); }
  .front-brand {
    position: absolute; left: 0; right: 0; top: 118px;
    text-align: center;
    font-weight: 700; font-size: 40px; letter-spacing: 10px;
    color: var(--red);
  }
  .front-handle {
    position: absolute; left: 26px; bottom: 12px;
    display: flex; align-items: center; gap: 10px;
    font-size: 14px; color: var(--ink);
  }
  .handle-dot { width: 10px; height: 10px; border-radius: 50%; background: var(--red); }

  /* Back */
  .card-back { left: 570px; top: 480px; background: var(--white); }
  .back-brand { position: absolute; left: 34px; top: 92px; }
  .brand-name {
    font-weight: 400; font-size: 38px; letter-spacing: 12px;
    color: var(--ink); line-height: 1;
  }
  .brand-rule { height: 1px; background: var(--rule); margin: 6px 0 4px; width: 220px; }
  .brand-tagline {
    font-size: 10px; font-weight: 500; letter-spacing: 3.2px;
    color: var(--red);
  }
  .person { position: absolute; right: 34px; top: 34px; text-align: right; }
  .person-first, .person-last {
    font-weight: 700; font-size: 22px; color: var(--wine); line-height: 1.1;
  }
  .person-role, .person-title { font-size: 12px; color: var(--ink); line-height: 1.3; }
  .person-rule { height: 1px; background: var(--rule); margin-top: 4px; width: 260px; margin-left: auto; }

  .contact {
    position: absolute; left: 34px; bottom: 26px; width: 240px;
    border-top: 1px solid var(--rule); padding-top: 8px;
    list-style: none;
  }
  .contact li {
    display: flex; align-items: center; gap: 10px;
    font-size: 14px; color: var(--ink); line-height: 1.35;
  }
  .contact svg { width: 11px; height: 11px; flex: none; }
</style>
</head>
<body>

<section class="card card-front" aria-label="Anverso">
  <svg class="card-shapes" viewBox="0 0 560 320" aria-hidden="true">
    <polygon points="0,276 240,276 292,300 340,320 0,320" fill="var(--white)"/>
    <polygon points="292,300 560,228 560,250 340,320" fill="var(--red)"/>
  </svg>
  <div class="front-brand">ULMIRA</div>
  <div class="front-handle"><span class="handle-dot"></span>@ulmiraAT</div>
</section>

<section class="card card-back" aria-label="Reverso">
  <svg class="card-shapes" viewBox="0 0 560 320" aria-hidden="true">
    <polygon points="410,244 420,214 560,214 560,320 402,320" fill="var(--gray)"/>
    <polygon points="416,240 430,206 560,206 560,246 416,246" fill="var(--wine)"/>
  </svg>

  <div class="back-brand">
    <div class="brand-name">ULMIRA</div>
    <div class="brand-rule"></div>
    <div class="brand-tagline">ARQUITECTURA TÉCNICA</div>
  </div>

  <div class="person">
    <div class="person-first">Mauricio Gonzalo</div>
    <div class="person-role">COO</div>
    <div class="person-last">Pereda Villalta</div>
    <div class="person-title">Director de Operaciones</div>
    <div class="person-rule"></div>
  </div>

  <ul class="contact">
    <li>
      <svg viewBox="0 0 12 12"><path d="M2.5 1l2 2.2-1 1.3a6 6 0 0 0 4 4l1.3-1 2.2 2-1.2 1.5C5.5 11 1 6.5 1 2.2z" fill="var(--red)"/></svg>
      (+571) 555 010 0199
    </li>
    <li>
      <svg viewBox="0 0 12 12"><rect x="1" y="2.5" width="10" height="7" fill="none" stroke="var(--red)" stroke-width="1.3"/><path d="M1 3l5 3.5L11 3" fill="none" stroke="var(--red)" stroke-width="1.3"/></svg>
      info@ulmira-example.com
    </li>
    <li>
      <svg viewBox="0 0 12 12"><circle cx="6" cy="6" r="5" fill="none" stroke="var(--red)" stroke-width="1.3"/><path d="M1 6h10M6 1c-3 3-3 7 0 10M6 1c3 3 3 7 0 10" fill="none" stroke="var(--red)" stroke-width="1"/></svg>
      www.ulmira-example.com
    </li>
  </ul>
</section>

</body>
</html>
```